Boutique custom software development company needs new business card

Our nearly 20 year old custom software development company would like to better include the fact that we are now providing Bitcoin services. These new services are B2B include education (how to acquire and securely hold Bitcoin) and integrating Bitcoin payments into existing ecommerce sites or other existing systems. Please keep the card clean and simple. Attached is our current design and some other files. vextorial.com

Target Market(s)

businesses owners interested in long term relationship

Industry/Entity Type

Custom software development and Bitcoin

Contact Information for Business Card

Dale Parker, dale@vextorial.com, vextorial.com, (888) 555-VXTRL

Font styles to use
Other font styles liked:
• monospace

Requirements
Must have
• double-sided
Nice to have
• clean and simple
Should not have
• physical address

```html
<!DOCTYPE html>
<html lang="en">
<head>
<meta charset="utf-8">
<title>Vextorial — Business Card</title>
<link rel="stylesheet" href="https://fonts.googleapis.com/css2?family=Poppins:wght@400;600;700&family=Open+Sans:wght@400&display=swap">
<style>
  :root {
    --backdrop: #2a2522;
    --card: #1b1b1b;
    --blue: #4274c0;
    --orange: #f37f22;
    --white: #ffffff;
  }
  * { margin: 0; padding: 0; box-sizing: border-box; }
  html, body { width: 1200px; height: 842px; overflow: hidden; }
  body {
    background: var(--backdrop);
    display: flex;
    align-items: center;
    justify-content: center;
    gap: 50px;
  }
  .card {
    position: relative;
    width: 525px;
    height: 300px;
    background: var(--card);
    overflow: hidden;
    box-shadow: 0 18px 40px rgba(0,0,0,0.55);
  }

  /* Contact side */
  .card--contact .band {
    position: absolute;
    left: 0; right: 0;
    height: 14px;
    background: var(--blue);
  }
  .card--contact .band--top { top: 0; }
  .card--contact .band--bottom { bottom: 0; }
  .contact {
    position: absolute;
    inset: 0;
    display: flex;
    flex-direction: column;
    align-items: center;
    justify-content: center;
    font-family: "Poppins", sans-serif;
  }
  .contact__name {
    color: var(--orange);
    font-weight: 600;
    font-size: 22px;
    letter-spacing: 1px;
    text-transform: uppercase;
  }
  .contact__rule {
    width: 50px;
    height: 2px;
    background: var(--blue);
    margin: 10px 0 14px;
  }
  .contact__line {
    color: var(--white);
    font-size: 15px;
    line-height: 1.3;
  }

  /* Brand side */
  .accent {
    position: absolute;
    display: flex;
    gap: 6px;
  }
  .accent__block { width: 30px; height: 80px; background: var(--blue); }
  .accent__stripe { width: 4px; height: 80px; background: var(--orange); }
  .accent--left { left: 0; top: 150px; }
  .accent--right { right: 0; top: 38px; flex-direction: row-reverse; }
  .brand {
    position: absolute;
    left: 120px;
    right: 70px;
    top: 100px;
    display: flex;
    flex-direction: column;
    align-items: flex-end;
  }
  .brand__name {
    font-family: "Poppins", sans-serif;
    font-weight: 700;
    font-size: 46px;
    line-height: 1;
    color: var(--blue);
    letter-spacing: 1px;
  }
  .brand__tagline {
    font-family: "Open Sans", sans-serif;
    font-size: 16px;
    line-height: 1.3;
    color: var(--blue);
    margin-top: 8px;
    text-align: right;
  }
</style>
</head>
<body>
  <section class="card card--contact">
    <div class="band band--top"></div>
    <div class="contact">
      <h1 class="contact__name">Dale Parker</h1>
      <div class="contact__rule"></div>
      <p class="contact__line">(888) 555-VXTRL</p>
      <p class="contact__line">dale@vextorial.com</p>
      <p class="contact__line">www.vextorial.com</p>
    </div>
    <div class="band band--bottom"></div>
  </section>

  <section class="card card--brand">
    <div class="accent accent--left">
      <span class="accent__block"></span>
      <span class="accent__stripe"></span>
    </div>
    <div class="accent accent--right">
      <span class="accent__block"></span>
      <span class="accent__stripe"></span>
    </div>
    <div class="brand">
      <p class="brand__name">VEXTORIAL</p>
      <p class="brand__tagline">developer of custom applications<br>&amp; bitcoin services</p>
    </div>
  </section>
</body>
</html>
```